Business Card for Polygraph business in Africa

Business Card . Polygraph Examiner based in Tanzania, East Africa.
Business Card will be used to disseminate contact information to potential clients.
It should convey that I am a professional specifically in the polygraph field and perform my work with integrity.

I have attached the business card that I'm currently using, which I threw together myself initially. It's not professional enough.

Target Market(s)

Banks, Accounting Firms, Government Ministries, Gas, Oil, & Gemstone Mining Concerns, Wildlife Conservation NGOs, International companies located in East Africa.

Industry/Entity Type

Business

Contact Information for Business Card

Veritrace Kilonga
Miriam Holloway
PO Box 48317
Arusha, Tanzania
+255 612 839 274
miriamholloway@postvale.example

Colors
00a990
f37122
faa54b

Requirements
Must have
• - Veritrace Kilonga (with the word "Polygraph" being more prominent than the word "Tanzania")
• - Forensic Examinations
• - Employment Screening
• - Should contain a logo of the Continental Truthline Society (of which I'm a member)
• - I would like an accent design (such as the polygraph "squiggles" of a cardio tracing or such as that)
• - My contact information (less prominent, but large enough to read legibly). I would also consider putting the contact information on the second side of the card.
Nice to have
• My color suggestions are changeable.
Should not have
• Anything "cutesy" or "cartoonish"

```html
<!DOCTYPE html>
<html lang="en">
<head>
<meta charset="utf-8">
<title>Veritrace Kilonga – Business Card</title>
<link rel="stylesheet" href="https://fonts.googleapis.com/css2?family=Roboto:wght@400;700&family=Roboto+Condensed:wght@700&display=swap">
<style>
  :root {
    --brand-blue: #02468f;
    --ink-grey: #5f5f5f;
    --band-grey: #5c5c5c;
    --paper: #f7f7f7;
    --backdrop: #e6e6e6;
    --white: #ffffff;
  }
  html, body {
    margin: 0;
    width: 1200px;
    height: 960px;
    overflow: hidden;
    background: var(--backdrop);
    font-family: "Roboto", Arial, sans-serif;
  }
  .stage { position: relative; width: 1200px; height: 960px; }

  .card {
    position: absolute;
    width: 600px;
    height: 342px;
    box-shadow: 0 3px 8px rgba(0,0,0,0.25);
    overflow: hidden;
  }
  .card-front { left: 314px; top: 113px; background: var(--paper); }
  .card-back  { left: 312px; top: 472px; background: var(--brand-blue); }

  /* front: wordmark */
  .wordmark {
    position: absolute;
    left: 192px; top: 97px;
    margin: 0;
    font-size: 26px;
    font-weight: 700;
    letter-spacing: 0.5px;
    color: var(--brand-blue);
    white-space: nowrap;
  }
  .tagline {
    position: absolute;
    left: 192px; top: 128px;
    width: 296px;
    border-top: 2px solid #8a8a8a;
    padding-top: 3px;
    font-size: 10.5px;
    letter-spacing: 0.4px;
    color: var(--ink-grey);
    white-space: nowrap;
  }

  .society-seal {
    position: absolute;
    left: 508px; top: 22px;
    width: 68px; height: 68px;
    border-radius: 50%;
    background: var(--white);
    border: 3px solid var(--brand-blue);
    box-sizing: border-box;
  }

  /* front: identity block */
  .identity {
    position: absolute;
    right: 303px; top: 196px;
    text-align: right;
    white-space: nowrap;
  }
  .person-name {
    margin: 0;
    font-family: "Roboto Condensed", Arial, sans-serif;
    font-size: 21px;
    font-weight: 700;
    color: var(--brand-blue);
    line-height: 26px;
  }
  .company-name {
    font-size: 15px;
    color: var(--ink-grey);
    line-height: 20px;
    letter-spacing: 0.3px;
  }
  .postal-address {
    font-size: 14px;
    color: var(--ink-grey);
    line-height: 20px;
    font-style: normal;
  }

  .divider {
    position: absolute;
    left: 314px; top: 190px;
    width: 1px; height: 80px;
    background: #9a9a9a;
  }

  .contact-list {
    position: absolute;
    left: 334px; top: 200px;
    margin: 0; padding: 0;
    list-style: none;
    font-size: 14px;
    color: var(--ink-grey);
    line-height: 19.5px;
    white-space: nowrap;
  }
  .contact-list li { display: flex; align-items: center; gap: 8px; }
  .contact-list svg { width: 13px; height: 13px; fill: var(--brand-blue); flex: none; }

  .band-blue {
    position: absolute;
    left: 0; top: 329px;
    width: 394px; height: 13px;
    background: var(--brand-blue);
  }
  .band-grey {
    position: absolute;
    left: 390px; top: 329px;
    width: 210px; height: 13px;
    background: var(--band-grey);
    clip-path: polygon(6px 0, 100% 0, 100% 100%, 0 100%);
    border-left: 4px solid var(--paper);
  }

  /* back */
  .back-name {
    position: absolute;
    left: 0; right: 0; top: 150px;
    margin: 0;
    text-align: center;
    font-size: 26px;
    font-weight: 700;
    letter-spacing: 0.5px;
    color: var(--white);
  }
  .back-web {
    position: absolute;
    left: 0; right: 0; top: 292px;
    text-align: center;
    font-size: 14px;
    letter-spacing: 5px;
    color: var(--white);
  }
</style>
</head>
<body>
<main class="stage">

  <section class="card card-front" aria-label="Business card front">
    <h1 class="wordmark">VERITRACE KILONGA</h1>
    <div class="tagline">FORENSIC EXAMINATIONS &#9679; EMPLOYMENT SCREENING</div>

    <div class="society-seal" role="img" aria-label="Continental Truthline Society membership seal"></div>

    <div class="identity">
      <h2 class="person-name">MIRIAM HOLLOWAY</h2>
      <div class="company-name">VERITRACE KILONGA</div>
      <address class="postal-address">PO Box 48317, Arusha, Tanzania</address>
    </div>

    <div class="divider"></div>

    <ul class="contact-list">
      <li>
        <svg viewBox="0 0 24 24" aria-hidden="true"><path d="M6.6 10.8a15.1 15.1 0 0 0 6.6 6.6l2.2-2.2c.3-.3.7-.4 1-.2 1.1.4 2.3.6 3.6.6.6 0 1 .4 1 1V20c0 .6-.4 1-1 1A17 17 0 0 1 3 4c0-.6.4-1 1-1h3.5c.6 0 1 .4 1 1 0 1.3.2 2.5.6 3.6.1.3 0 .7-.2 1z"/></svg>
        <span>+255 612 839 274</span>
      </li>
      <li>
        <svg viewBox="0 0 24 24" aria-hidden="true"><path d="M2 5h20v14H2z M2 5l10 8 10-8" fill="none" stroke="#02468f" stroke-width="0"/><path d="M2 6.5V19h20V6.5l-10 7.5z M3 5l9 6.8L21 5z"/></svg>
        <span>miriamholloway@postvale.example</span>
      </li>
      <li>
        <svg viewBox="0 0 24 24" aria-hidden="true"><circle cx="12" cy="12" r="10"/><path d="M2 12h20M12 2c3 3 3 17 0 20M12 2c-3 3-3 17 0 20" fill="none" stroke="#f7f7f7" stroke-width="1.5"/></svg>
        <span>www.miriamholloway.example</span>
      </li>
    </ul>

    <div class="band-blue"></div>
    <div class="band-grey"></div>
  </section>

  <section class="card card-back" aria-label="Business card back">
    <p class="back-name">VERITRACE KILONGA</p>
    <div class="back-web">www.miriamholloway.example</div>
  </section>

</main>
</body>
</html>
```